Browser extension - redesign of extension and website

We need style improvement of our website for extension Dusk Lens (https://dusklens.example) and (https://store.example/detail/dark-mode-dusk-lens/qwpzrtyvbnmkhgfdsaxcvplokijuhyt) that incorporated dark mode in it heart. The main purpose of the extension is transforming webpages to "dark mode" and to apply many other filters for more pleasant viewing in dark environment. The final design should communicate safety, professional and love of dark mode.
What we need:
- Improved color schema - that is modern and reflect the purpose of the app (it will be used for both the website and the extension)
- Improved Logo based on current logo
- Style guide - for website and extension
- Good UI/UX for the flows of website - based on the purpose to download the extension. The user should be guided to see what the extension do and after that to download the extension
- Webpages that we need design for:
- Home page (https://dusklens.example),
- How to Start Page (https://dusklens.example/how-to-start/),
- Client Area (https://billing.dusklens.example/client/login),
- FAQ (https://dusklens.example/help/) ,
- Browser Template 1 (https://dusklens.example/chrome-dark-mode/)
- Browser Template 2 (https://dusklens.example/firefox-dark-mode/)
-Activation Instructions - https://dusklens.example/activation-instructions/

We are attaching our logo for reference and screenshots of our current website.

Please start with home page design first and extension home page, after submitting that we will evaluate and proceed accordingly.

Target Market(s)

Everyone who likes dark mode from 18+ till 65+ so we can make easy for them to read at dark places.

Industry/Entity Type

Software

Number of Pages Required

5+ page

Font styles to use
Sans Serif

Requirements
Must have
• Dark color scheme, To inspire confidence in an extension,
Should not have
• Do not use pure black as background.

```html
<!DOCTYPE html>
<html lang="en">
<head>
<meta charset="utf-8">
<title>Dusk Lens – Dark mode on any website</title>
<link rel="stylesheet" href="https://fonts.googleapis.com/css2?family=Open+Sans:wght@300;400;600;700&display=swap">
<style>
:root{
  --canvas:#d6d6d6;
  --teal:#1f9fae;
  --ink:#ffffff;
  --muted:#d8d8d8;
  --grey:#6a6a6a;
  --dark:#262626;
  --darker:#171717;
  --line:#cfcfcf;
}
*{box-sizing:border-box;margin:0;padding:0}
html,body{width:1200px;height:4000px;overflow:hidden;background:var(--canvas);font-family:"Open Sans",Arial,sans-serif;color:var(--ink)}
.page{position:absolute;left:122px;top:0;width:956px;height:3822px;background:var(--grey);overflow:hidden}
.abs{position:absolute}
.center{text-align:center;left:0;right:0}
.brand{display:flex;align-items:center;color:var(--teal);font-weight:700;letter-spacing:1px}
/* nav */
.nav{top:0;left:0;width:956px;height:70px;background:var(--darker);display:flex;align-items:center;justify-content:space-between;padding:0 40px 0 22px}
.nav .brand{font-size:30px}
.nav ul{display:flex;gap:48px;list-style:none;font-size:16px}
/* hero */
.hero{top:70px;left:0;width:956px;height:536px;background:linear-gradient(160deg,#3b3328 0%,#1b2324 45%,#2a3a36 70%,#141414 100%);border-radius:0 0 50% 50%/0 0 150px 150px;border-bottom:3px solid #9a9a9a;overflow:hidden}
.hero h1{top:140px;font-weight:300;font-size:38px;line-height:48px;letter-spacing:.5px}
.hero mark{background:#fff;color:#111;font-weight:700;padding:0 4px}
.hero p{top:240px;font-size:16px}
.btn{top:320px;left:382px;width:192px;height:28px;background:#fff;color:#111;font-size:17px;letter-spacing:.5px;text-align:center;line-height:28px;border-radius:2px}
/* section heads */
.head{font-size:31px;font-weight:700;letter-spacing:1.5px}
.head u{text-decoration:none;border-bottom:2px solid #fff;padding-bottom:2px}
.head .light{font-weight:400}
.sub{font-size:13px;line-height:16px;color:var(--muted)}
/* features */
.fcard{top:793px;height:270px;border:2px solid var(--line);border-radius:8px;text-align:center;padding:12px 12px 0}
.fcard.on{background:linear-gradient(180deg,#2a2a2a,#4b4b4b 70%,#5e5e5e);border-color:#444}
.ficon{width:72px;height:72px;border-radius:50%;margin:0 auto 24px;display:flex;align-items:center;justify-content:center;background:#fff}
.fcard:not(.on) .ficon{background:#1b1b1b;border:2px solid #fff}
.fcard h3{font-size:13px;font-weight:600;letter-spacing:1px;margin-bottom:14px}
.fcard p{font-size:9.5px;line-height:12px;color:var(--muted)}
/* video */
.video-band{top:1154px;left:0;width:956px;height:354px;background:var(--dark)}
.video{top:25px;left:33px;width:537px;height:300px;background:radial-gradient(ellipse at 50% 50%,#d8e6ff 0%,#6b4bd9 18%,#2b1770 38%,#0b0b1c 70%);overflow:hidden}
.video .vt{top:12px;left:14px;font-size:11px}
.video .play{top:128px;left:246px;width:44px;height:44px}
.video .wo{bottom:10px;left:14px;font-size:10px}
.latest{top:45px;left:620px;width:310px}
.latest h2{font-size:21px;font-weight:600;letter-spacing:1.5px;margin-bottom:18px}
.latest li{list-style:none;font-size:13.5px;line-height:25px;padding-left:20px;position:relative}
.latest li::before{content:"";position:absolute;left:0;top:8px;width:9px;height:9px;border:2px solid #fff;border-radius:50%}
/* partners */
.partners{top:1508px;left:0;width:956px;height:150px;background:var(--darker);display:flex;align-items:center;justify-content:space-around;padding:0 40px;font-size:24px;font-weight:600;color:#c9c9c9}
/* benefits */
.benefits{top:1658px;left:0;width:956px;height:577px;background:var(--dark)}
.bitem{width:260px;text-align:center}
.bitem svg{display:block;margin:0 auto 10px}
.bitem h3{font-size:21px;font-weight:600;margin-bottom:6px}
.bitem p{font-size:10.5px;line-height:13px;color:var(--muted)}
/* plans */
.pcard{top:2411px;height:269px;border:2px solid var(--line);border-radius:8px;text-align:center;padding-top:14px}
.pcard.on{background:linear-gradient(180deg,#2a2a2a,#4d4d4d 70%,#5f5f5f);border-color:#444}
.pcard h3{font-size:28px;font-weight:600;margin-bottom:10px}
.pcard h3 span{font-weight:300}
.pcard.on h3{font-weight:400;text-decoration:underline;text-underline-offset:6px;text-decoration-thickness:1px}
.pcard li{list-style:none;font-size:12.5px;line-height:30px}
.pcard .sel{position:absolute;bottom:16px;left:0;right:0;font-size:26px;font-weight:600;letter-spacing:1px}
/* news */
.news{top:2759px;left:0;width:956px;height:526px;background:var(--darker)}
.ncard{background:#646464}
.nshot{background:linear-gradient(135deg,#2f3f5c,#5a6b8f 50%,#1a2133)}
.ncard .date{font-size:11px}
.ncard h4{font-size:12px;font-weight:700;line-height:15px}
.ncard .more{position:absolute;right:10px;bottom:6px;font-size:10px}
/* browsers */
.bnames{top:3418px;left:30px;width:896px;display:flex;justify-content:space-between;font-size:15px;font-weight:600;color:#e6e6e6}
/* footer */
.footer{top:3480px;left:-60px;width:1076px;height:360px;background:var(--darker);border-radius:50% 50% 0 0/130px 130px 0 0;border-top:3px solid #8a8a8a}
.footer .brand{position:absolute;top:92px;left:0;right:0;justify-content:center;font-size:60px;font-weight:600}
.fnav{top:212px;left:60px;width:956px;display:flex;justify-content:center;gap:52px;list-style:none;font-size:17px}
.frule{top:252px;left:60px;width:956px;height:1px;background:#3c3c3c}
.social{top:282px;left:60px;width:956px;display:flex;justify-content:center;gap:46px;font-size:14px;font-weight:600}
</style>
</head>
<body>
<div class="page">

  <nav class="nav abs">
    <div class="brand">DUSK LENS</div>
    <ul><li>Home</li><li>How to start</li><li>Client</li><li>FAQ</li></ul>
  </nav>

  <header class="hero abs" role="img" aria-label="Photo of developers working at night in a dim office with glowing monitors">
    <h1 class="abs center" style="text-align:center">PROTECT YOUR EYES, ENABLE <mark>DARK</mark><br><mark>MODE</mark> ON ANY WEBSITE!</h1>
    <p class="abs center" style="text-align:center">Smart conversion, no ads, no data mining, helpful support!</p>
    <div class="btn abs">DOWNLOAD NOW</div>
  </header>

  <section>
    <h2 class="head abs center" style="top:670px;text-align:center"><u>OUR FEATURES</u></h2>
    <p class="sub abs" style="top:726px;left:180px;width:596px;text-align:center">Lorem Ipsum is simply dummy text of the printing and typesetting industry. Lorem Ipsum has been the industry's standard dummy text ever since the 1500s</p>

    <div class="fcard on abs" style="left:22px;width:218px">
      <div class="ficon"><svg width="34" height="34" viewBox="0 0 34 34" fill="none" stroke="#222" stroke-width="2"><path d="M8 26l3-9 12-12 6 6-12 12z"/><path d="M20 8l6 6"/></svg></div>
      <h3>SMART CONVERSION</h3>
      <p>Instead of inverting, we are converting the colors. Unlike its competitors, Dusk Lens takes a unique approach to each webpage. It analyses the page colors and converts them in a way to provide you with smooth and consistent dark mode. No simple color inversions, no bright spots and flashes.</p>
    </div>
    <div class="fcard abs" style="left:253px;width:220px">
      <div class="ficon"><svg width="38" height="24" viewBox="0 0 38 24" fill="none" stroke="#fff" stroke-width="2.5"><path d="M2 12C8 3 30 3 36 12 30 21 8 21 2 12z"/><circle cx="19" cy="12" r="5"/></svg></div>
      <h3>PROTECT YOUR EYES</h3>
      <p>Staring at your screen for 10-12 hours a day is surely taking toll on your eyes. Having dark mode that is consistent on all websites is the best way to reduce the eye strain, headache and watery eyes.</p>
    </div>
    <div class="fcard abs" style="left:482px;width:222px">
      <div class="ficon"><svg width="34" height="34" viewBox="0 0 34 34" fill="none" stroke="#fff" stroke-width="2.2"><path d="M7 18v-3a10 10 0 0 1 20 0v3"/><rect x="5" y="17" width="5" height="8" rx="2"/><rect x="24" y="17" width="5" height="8" rx="2"/><path d="M27 25c0 4-4 5-8 5"/></svg></div>
      <h3>HELPFUL SUPPORT</h3>
      <p>Helpful support, ready to answer your questions. We built an internal chat system that you can use to reach out to us directly from the extension. Encountered a broken website, we are here to fix it for you.</p>
    </div>
    <div class="fcard abs" style="left:716px;width:221px">
      <div class="ficon"><svg width="36" height="36" viewBox="0 0 36 36" fill="none" stroke="#fff" stroke-width="2.2"><circle cx="18" cy="18" r="14"/><path d="M8 28L28 8"/></svg></div>
      <h3>NO ADS &amp; DATA MINING</h3>
      <p>Dusk Lens does not monitor, process nor store your browsing activity. No ads even on the Lite (free version).</p>
    </div>
  </section>

  <section class="video-band abs">
    <div class="video abs" role="img" aria-label="Video preview showing a glowing stylised eye on a dark background">
      <span class="vt abs">Dark Mode - Dusk Lens Extension - on any website</span>
      <svg class="play abs" viewBox="0 0 44 44"><circle cx="22" cy="22" r="22" fill="#fff"/><path d="M17 13l14 9-14 9z" fill="#222"/></svg>
      <span class="wo abs">Watch on Clipstream</span>
    </div>
    <div class="latest abs">
      <h2>LATEST VERSION</h2>
      <ul>
        <li>Trackboard dark mode - custom theme</li>
        <li>Wikispace dark mode - custom theme</li>
        <li>Codebin dark mode - custom theme</li>
        <li>NORMAL mode - mutator - to add missing attribute</li>
        <li>Shopgrid.example - product image dark mode</li>
        <li>Change order of injected custom code</li>
      </ul>
    </div>
  </section>

  <section class="partners abs" aria-label="Companies using the extension">
    <span>Taskmill</span><span>Redcrest</span><span>Corvane</span><span>Metrisca</span><span>Chatterly</span><span>Quorix</span>
  </section>

  <section class="benefits abs">
    <h2 class="head abs center" style="top:58px;text-align:center"><u>BENEFITS OF DARK WEB</u></h2>
    <p class="sub abs" style="top:112px;left:130px;width:696px;text-align:center">Dusk Lens extension is a great tool to protect your eyes if you are browsing late at night, working in in low-light environment or read extensively.</p>

    <div class="bitem abs" style="top:172px;left:50px">
      <svg width="40" height="40" viewBox="0 0 40 40"><circle cx="20" cy="20" r="17" fill="none" stroke="#fff" stroke-width="3"/><path d="M20 3a17 17 0 0 1 0 34z" fill="#fff"/></svg>
      <h3>Color changer</h3><p>Reinvent your browsing experience by changing any color on any website. You can customise a single website or all with couple of clicks.</p>
    </div>
    <div class="bitem abs" style="top:172px;left:348px">
      <svg width="40" height="40" viewBox="0 0 40 40" stroke="#fff" stroke-width="2.5" fill="none"><circle cx="20" cy="20" r="7"/><path d="M20 3v6M20 31v6M3 20h6M31 20h6M8 8l4 4M28 28l4 4M8 32l4-4M28 12l4-4"/></svg>
      <h3>Brightness</h3><p>Adjust the brightness, the contrast and the saturation to match the recommended healthy levels and protect your eyes.</p>
    </div>
    <div class="bitem abs" style="top:172px;left:646px">
      <svg width="40" height="40" viewBox="0 0 40 40" stroke="#fff" stroke-width="2.2" fill="none"><path d="M4 10q4-4 8 0t8 0 8 0 8 0M4 18q4-4 8 0t8 0 8 0 8 0M4 26q4-4 8 0t8 0 8 0 8 0M4 33h32"/></svg>
      <h3>Dimming</h3><p>Extremely useful if you are working in dark space/room and the screen is the only source of light in the room.</p>
    </div>
    <div class="bitem abs" style="top:382px;left:50px">
      <svg width="40" height="40" viewBox="0 0 40 40" stroke="#fff" stroke-width="2.2" fill="none"><rect x="3" y="11" width="34" height="23" rx="3"/><path d="M13 11l3-5h8l3 5"/><circle cx="20" cy="22" r="6"/></svg>
      <h3>Image Conversion</h3><p>We analyse and convert only the small images and icons in a website to give you even smoother experience. Social feed posts and other significant media is not converted.</p>
    </div>
    <div class="bitem abs" style="top:382px;left:348px">
      <svg width="40" height="40" viewBox="0 0 40 40" stroke="#fff" stroke-width="3" fill="none"><circle cx="20" cy="20" r="6"/><circle cx="20" cy="20" r="12" stroke-dasharray="5 4"/><path d="M20 2v6M20 32v6M2 20h6M32 20h6"/></svg>
      <h3>Blue Light Filter</h3><p>Take care of your eyes by eliminating the blue light coming from your screen. Highly recommended especially during late night browsing.</p>
    </div>
    <div class="bitem abs" style="top:382px;left:646px">
      <svg width="40" height="40" viewBox="0 0 40 40" stroke="#fff" stroke-width="2.2" fill="none"><circle cx="20" cy="12" r="8"/><path d="M5 37c0-9 6-14 15-14s15 5 15 14z"/></svg>
      <h3>Real Support</h3><p>We DO provide support to everyone who installed the extension. Simply use our messaging center by opening the extension.</p>
    </div>
  </section>

  <section>
    <h2 class="head abs center" style="top:2296px;text-align:center"><u>PLANS</u></h2>
    <p class="abs" style="top:2348px;left:80px;width:796px;text-align:center;font-size:15px;line-height:17px">Install now and get 3 months of Dusk Lens Pro for free!<br><span style="font-size:13px">Afterwards the price is a little over 2 cents per day or you can choose the free version - Dusk Lens Lite</span></p>

    <div class="pcard on abs" style="left:22px;width:218px"><h3>FREE</h3><ul><li>Upto 1 Browser</li><li>5 Websites</li><li>Any Website</li><li>Available on All Browser</li><li>Help 24/7</li></ul><div class="sel">SELECT</div></div>
    <div class="pcard abs" style="left:253px;width:220px"><h3>$9 <span>/ Yearly</span></h3><ul><li>Upto 3 Browser</li><li>Unlimited Websites</li><li>Any Website</li><li>Available on All Browser</li><li>Help 24/7</li></ul><div class="sel">SELECT</div></div>
    <div class="pcard abs" style="left:482px;width:222px"><h3>$14 <span>/ Yearly</span></h3><ul><li>Upto 6 Browser</li><li>Unlimited Websites</li><li>Any Website</li><li>Available on All Browser</li><li>Help 24/7</li></ul><div class="sel">SELECT</div></div>
    <div class="pcard abs" style="left:716px;width:221px"><h3>$40 <span style="font-size:22px">/ One-time</span></h3><ul><li>Upto 10 Browser</li><li>Unlimited Websites</li><li>Any Website</li><li>Available on All Browser</li><li>Help 24/7</li></ul><div class="sel">SELECT</div></div>
  </section>

  <section class="news abs">
    <h2 class="head abs center" style="top:50px;text-align:center"><u>DUSK LENS</u> <span class="light">IN THE NEWS</span></h2>
    <p class="sub abs" style="top:102px;left:180px;width:596px;text-align:center">Lorem Ipsum is simply dummy text of the printing and typesetting industry. Lorem Ipsum has been the industry's standard dummy text ever since the 1500s</p>

    <article class="ncard abs" style="top:177px;left:106px;width:319px;height:295px">
      <div class="nshot abs" role="img" aria-label="Screenshot of a blogging site shown in dark mode" style="top:4px;left:4px;width:311px;height:196px;background:linear-gradient(90deg,#f2f2f2 0 55%,#2c2c2c 55%)"></div>
      <span class="date abs" style="top:212px;left:14px">25-NOV-2022</span>
      <h4 class="abs" style="top:228px;left:14px;font-size:21px;font-weight:600;line-height:26px;letter-spacing:.5px">NOW ON PINWAVE</h4>
      <span class="more">READ MORE</span>
    </article>
    <article class="ncard abs" style="top:177px;left:480px;width:320px;height:134px">
      <div class="nshot abs" role="img" aria-label="Photo of a person reading a phone in bed at night" style="top:0;left:0;width:170px;height:134px"></div>
      <span class="date abs" style="top:8px;left:180px">25-NOV-2022</span>
      <h4 class="abs" style="top:24px;left:180px;width:120px">ORBIT NEWS - READ THE NEWS IN DARK MODE</h4>
      <span class="more">READ MORE</span>
    </article>
    <article class="ncard abs" style="top:338px;left:480px;width:320px;height:134px">
      <div class="nshot abs" role="img" aria-label="Photo of a desk with a laptop lit by purple and blue light" style="top:0;left:0;width:170px;height:134px;background:linear-gradient(135deg,#3a1a5c,#a03aa0 50%,#1f2d6a)"></div>
      <span class="date abs" style="top:8px;left:180px">25-NOV-2022</span>
      <h4 class="abs" style="top:24px;left:180px;width:120px">ORBIT NEWS - READ THE NEWS IN DARK MODE</h4>
      <span class="more">READ MORE</span>
    </article>
  </section>

  <section>
    <h2 class="head abs center" style="top:3342px;text-align:center"><u>AVAILABLE</u> <span class="light">IN EVERY BROWSER</span></h2>
    <div class="bnames abs" aria-label="Supported browsers">
      <span>Glint</span><span>Emberfox</span><span>Ridge</span><span>Voyage</span><span>Aria</span><span>Yonder</span><span>Kite</span><span>Verdant</span><span>Bold</span>
    </div>
  </section>

  <footer class="footer abs">
    <div class="brand">DUSK LENS</div>
    <ul class="fnav abs"><li>Home</li><li>How to start</li><li>Install Now</li><li>Merchandise</li><li>FAQ</li></ul>
    <div class="frule abs"></div>
    <div class="social abs"><span>Chirpline</span><span>Workly</span><span>Clipstream</span><span>Friendnet</span><span>Snapgram</span></div>
  </footer>

</div>
</body>
</html>
```